Heron Loan Partners Business Card

We need a business card design for our mortgage servicing company. In addition to servicing the loans of homeowners, we help homeowners with purchasing their homes and any mortgage refinancing. We would like to see designs that use the colors in the logo attached below (gold-ish yellow and navy blue), and any other design you deem fit! The design should communicate a simpler life with smart mortgages provided by Heron.

```html
<!DOCTYPE html>
<html lang="en">
<head>
<meta charset="utf-8">
<title>Heron Loan Partners Business Card</title>
<link rel="stylesheet" href="https://fonts.googleapis.com/css2?family=Montserrat:wght@400;500;700;800&display=swap">
<style>
  :root {
    --backdrop: #2a2a2a;
    --card: #ffffff;
    --navy: #2b2660;
    --gold: #e0b23a;
    --ink: #1c1c1c;
  }
  html, body {
    margin: 0;
    padding: 0;
    width: 1200px;
    height: 960px;
    overflow: hidden;
    background: var(--backdrop);
    font-family: "Montserrat", sans-serif;
  }
  .sheet {
    position: relative;
    width: 1200px;
    height: 960px;
  }
  .card {
    position: absolute;
    left: 220px;
    width: 760px;
    height: 434px;
    background: var(--card);
    border-radius: 24px;
    overflow: hidden;
  }
  .card--front { top: 26px; }
  .card--back { top: 500px; }

  .wordmark {
    display: flex;
    align-items: center;
    gap: 14px;
    color: var(--navy);
    font-weight: 800;
    white-space: nowrap;
  }
  .wordmark__dot {
    border-radius: 50%;
    background: var(--navy);
    flex: none;
  }
  .card--front .wordmark {
    position: absolute;
    left: 0; right: 0; top: 0; bottom: 0;
    justify-content: center;
    font-size: 46px;
    letter-spacing: 0.5px;
  }
  .card--front .wordmark__dot { width: 34px; height: 34px; }

  .card--back .wordmark {
    position: absolute;
    right: 46px;
    top: 56px;
    font-size: 28px;
    gap: 10px;
  }
  .card--back .wordmark__dot { width: 22px; height: 22px; }

  .accent-block {
    position: absolute;
    left: 0;
    top: 186px;
    width: 36px;
    height: 64px;
    background: var(--gold);
  }
  .person {
    position: absolute;
    left: 54px;
    top: 180px;
  }
  .person__name {
    margin: 0;
    font-size: 26px;
    font-weight: 800;
    letter-spacing: 0.5px;
    color: var(--navy);
  }
  .person__name .surname { color: var(--gold); }
  .person__role {
    margin: 4px 0 0;
    font-size: 21px;
    font-weight: 500;
    color: var(--ink);
  }
  .address {
    position: absolute;
    right: 46px;
    top: 190px;
    margin: 0;
    font-style: normal;
    text-align: right;
    font-size: 20px;
    font-weight: 500;
    line-height: 1.45;
    color: var(--ink);
  }
  .contacts {
    position: absolute;
    left: 190px;
    bottom: 28px;
    margin: 0;
    padding: 0;
    list-style: none;
    font-size: 20px;
    font-weight: 500;
    color: var(--ink);
  }
  .contacts li {
    display: flex;
    align-items: center;
    gap: 14px;
    line-height: 1.55;
  }
  .contacts svg { width: 20px; height: 20px; flex: none; }
</style>
</head>
<body>
<main class="sheet">

  <section class="card card--front" aria-label="Card front">
    <div class="wordmark">
      <span class="wordmark__dot"></span>
      <span>Heron Loan Partners</span>
    </div>
  </section>

  <section class="card card--back" aria-label="Card back">
    <div class="wordmark">
      <span class="wordmark__dot"></span>
      <span>Heron Loan Partners</span>
    </div>

    <div class="accent-block"></div>
    <div class="person">
      <p class="person__name">DARA <span class="surname">WELLFORD</span></p>
      <p class="person__role">Owner</p>
    </div>

    <address class="address">482 Linden Ave, Ste<br>200, Austin, TX 78701</address>

    <ul class="contacts">
      <li>
        <svg viewBox="0 0 20 20" aria-hidden="true">
          <path fill="var(--gold)" d="M2 7c0-2 3-4 8-4s8 2 8 4v1.5h-4V6.8C13 6.3 11.6 6 10 6s-3 .3-4 .8v1.7H2z"/>
          <path fill="var(--gold)" d="M5 10h10l2 7H3z"/>
        </svg>
        <span>555.014.2290</span>
      </li>
      <li>
        <svg viewBox="0 0 20 20" aria-hidden="true">
          <rect x="1" y="4" width="18" height="12" rx="1.5" fill="var(--gold)"/>
          <path d="M1.5 5L10 11l8.5-6" fill="none" stroke="#fff" stroke-width="1.5"/>
        </svg>
        <span>info@heronloanpartners.com</span>
      </li>
      <li>
        <svg viewBox="0 0 20 20" aria-hidden="true">
          <circle cx="10" cy="10" r="8.5" fill="var(--gold)"/>
          <path d="M1.5 10h17M10 1.5c-3 3-3 14 0 17M10 1.5c3 3 3 14 0 17" fill="none" stroke="#fff" stroke-width="1.2"/>
        </svg>
        <span>www.heronloanpartners.com</span>
      </li>
    </ul>
  </section>

</main>
</body>
</html>
```